Construction business card

I need a new business card, they can connect with my logo, brand.
What we do is residential house , design and build
I like: Navy blue / black
I attached our logo, brand,
and, some idea for business card.

```html
<!DOCTYPE html>
<html lang="en">
<head>
<meta charset="utf-8">
<title>Harlow Ridge Builders — Business Card</title>
<link rel="stylesheet" href="https://fonts.googleapis.com/css2?family=Arimo:wght@400;700&display=swap">
<style>
  :root {
    --stage: #1c1c1d;
    --card: #2a2a2c;
    --gloss: #1b1b1c;
    --blue: #3d8ad6;
    --white: #ffffff;
    --text-soft: #e9e9ea;
  }
  * { box-sizing: border-box; margin: 0; padding: 0; }
  html, body { width: 1200px; height: 900px; overflow: hidden; }
  body {
    background: var(--stage);
    font-family: "Arimo", Arial, sans-serif;
    position: relative;
  }
  .card {
    position: absolute;
    left: 320px;
    width: 560px;
    height: 320px;
    border-radius: 18px;
    background: var(--card);
    overflow: hidden;
  }
  .card--front { top: 90px; }
  .card--back { top: 490px; }

  /* front: spot-gloss company name */
  .front-name {
    position: absolute;
    inset: 0;
    display: flex;
    align-items: center;
    justify-content: center;
    font-weight: 700;
    font-size: 34px;
    letter-spacing: 2px;
    text-transform: uppercase;
    color: var(--gloss);
  }

  /* back: brand block */
  .brand {
    position: absolute;
    left: 40px;
    top: 0;
    width: 240px;
    height: 290px;
    display: flex;
    align-items: center;
    gap: 10px;
  }
  .brand-mark {
    flex: none;
    width: 14px;
    height: 14px;
    background: var(--blue);
  }
  .brand-name {
    font-weight: 700;
    font-size: 22px;
    line-height: 1.15;
    letter-spacing: 1px;
    text-transform: uppercase;
    color: var(--white);
  }
  .divider {
    position: absolute;
    left: 300px;
    top: 70px;
    width: 1px;
    height: 150px;
    background: var(--blue);
  }
  .contact {
    position: absolute;
    left: 322px;
    top: 62px;
    color: var(--text-soft);
    font-size: 12px;
    line-height: 1.35;
  }
  .contact-name {
    color: var(--blue);
    font-weight: 700;
    font-size: 19px;
    letter-spacing: 0.5px;
    text-transform: uppercase;
  }
  .contact-role { margin-bottom: 14px; }
  .contact-address { margin-bottom: 14px; }
  .contact-list { list-style: none; }
  .contact-list li {
    display: flex;
    align-items: center;
    gap: 7px;
    margin-bottom: 3px;
  }
  .contact-list svg { width: 11px; height: 11px; flex: none; }

  .edge {
    position: absolute;
    left: 0;
    bottom: 0;
    width: 100%;
    height: 10px;
  }
</style>
</head>
<body>

<section class="card card--front" aria-label="Card front">
  <p class="front-name">Harlow Ridge Builders</p>
</section>

<section class="card card--back" aria-label="Card back">
  <div class="brand">
    <span class="brand-mark"></span>
    <p class="brand-name">Harlow Ridge<br>Builders</p>
  </div>

  <div class="divider"></div>

  <div class="contact">
    <p class="contact-name">Daniel Marsh</p>
    <p class="contact-role">CEO/Founder</p>
    <p class="contact-address">42 Ferncliff Rd,<br>Glen Ashby, VIC 3190</p>
    <ul class="contact-list">
      <li>
        <svg viewBox="0 0 24 24"><path fill="#3d8ad6" d="M6.6 10.8a15.1 15.1 0 0 0 6.6 6.6l2.2-2.2c.3-.3.7-.4 1-.2 1.1.4 2.3.6 3.6.6.6 0 1 .4 1 1V20c0 .6-.4 1-1 1A17 17 0 0 1 3 4c0-.6.4-1 1-1h3.5c.6 0 1 .4 1 1 0 1.3.2 2.5.6 3.6.1.3 0 .7-.2 1z"/></svg>
        0400 555 018
      </li>
      <li>
        <svg viewBox="0 0 24 24"><path fill="#3d8ad6" d="M2 5h20v14H2z"/><path fill="none" stroke="#2a2a2c" stroke-width="2" d="M2 5l10 8 10-8"/></svg>
        info@harlowridgebuilders.com.au
      </li>
      <li>
        <svg viewBox="0 0 24 24"><circle cx="12" cy="12" r="10" fill="#3d8ad6"/><path fill="none" stroke="#2a2a2c" stroke-width="1.5" d="M2 12h20M12 2c3 3 3 17 0 20M12 2c-3 3-3 17 0 20"/></svg>
        harlowridgebuilders.com.au
      </li>
    </ul>
  </div>

  <svg class="edge" viewBox="0 0 560 10" preserveAspectRatio="none" aria-hidden="true">
    <polygon points="0,0 330,0 322,10 0,10" fill="#3d8ad6"/>
    <polygon points="336,0 560,0 560,10 328,10" fill="#ffffff"/>
  </svg>
</section>

</body>
</html>
```